Business Card Design

I already have a company logo for my company. I have a logo for the manufacturer we represent. I want a professional business card design.

```html
<!DOCTYPE html>
<html lang="en">
<head>
<meta charset="utf-8">
<title>Beacon Signal Works LLC — Business Card</title>
<link href="https://fonts.googleapis.com/css2?family=Montserrat:wght@400;500;700;800&display=swap" rel="stylesheet">
<style>
  :root{
    --bg:#2a2d31;
    --card-black:#1c1c1e;
    --white:#ffffff;
    --red:#e3262b;
    --grey:#a9a9ad;
    --light:#e8e8ea;
    --ink:#1c1c1e;
  }
  *{box-sizing:border-box;margin:0;padding:0}
  html,body{width:1200px;height:900px;overflow:hidden}
  body{background:var(--bg);font-family:"Montserrat",sans-serif;position:relative}

  .card{position:absolute;width:540px;height:310px;border-radius:24px;overflow:hidden;background:var(--card-black);box-shadow:0 18px 40px rgba(0,0,0,.45)}
  .card--front{left:60px;top:500px}
  .card--back{left:600px;top:90px}

  /* front */
  .front-shape{position:absolute;inset:0}
  .wordmark{position:absolute;left:30px;top:28px;color:var(--light);font-weight:800;font-size:22px;line-height:1.05;letter-spacing:1.5px;text-transform:uppercase}
  .person{position:absolute;left:30px;top:104px}
  .person__name{color:var(--red);font-weight:700;font-size:19px}
  .person__role{color:var(--grey);font-size:10.5px;margin-top:2px}
  .address{position:absolute;left:30px;top:160px;color:var(--grey);font-size:10.5px;line-height:1.45}
  .contacts{position:absolute;left:30px;top:210px;list-style:none;color:var(--light);font-size:10.5px}
  .contacts li{display:flex;align-items:center;gap:8px;margin-bottom:6px}
  .contacts svg{width:10px;height:10px;flex:none}
  .front-mark{position:absolute;left:350px;top:140px;display:flex;align-items:center;gap:10px;color:var(--ink);font-weight:800;font-size:17px;letter-spacing:1px;line-height:1.1;text-transform:uppercase}
  .mark-dot{width:22px;height:22px;border-radius:50%;background:var(--red);flex:none}

  /* back */
  .back-mark{position:absolute;inset:0;display:flex;align-items:center;justify-content:center;gap:14px;color:var(--light);font-weight:800;font-size:26px;letter-spacing:2px;line-height:1.1;text-transform:uppercase}
  .back-mark .mark-dot{width:30px;height:30px}
</style>
</head>
<body>

  <section class="card card--front" aria-label="Business card front">
    <svg class="front-shape" viewBox="0 0 540 310" width="540" height="310" aria-hidden="true">
      <path d="M250 310 C228 170 320 42 540 30 L540 310 Z" fill="#ffffff"/>
      <path d="M238 304 C218 160 312 28 540 18" fill="none" stroke="#e3262b" stroke-width="2.5"/>
    </svg>

    <div class="wordmark">Beacon Signal<br>Works LLC</div>

    <div class="person">
      <p class="person__name">Dana Whitfield</p>
      <p class="person__role">Managing Director</p>
    </div>

    <p class="address">2840 Alder Row<br>Larkton, CO 80417</p>

    <ul class="contacts">
      <li>
        <svg viewBox="0 0 10 10"><path d="M2 0.5 L4 2.5 L3 4 Q4.5 6 6 7 L7.5 6 L9.5 8 L8 9.5 Q3 9 0.5 2 Z" fill="#e3262b"/></svg>
        555.214.0387
      </li>
      <li>
        <svg viewBox="0 0 10 10"><rect x="0.5" y="2" width="9" height="6.5" fill="#e3262b"/><path d="M0.5 2 L5 5.5 L9.5 2" fill="none" stroke="#1c1c1e" stroke-width="0.9"/></svg>
        hello@beaconsignalworks.com
      </li>
      <li>
        <svg viewBox="0 0 10 10"><circle cx="5" cy="5" r="4.3" fill="none" stroke="#e3262b" stroke-width="1.2"/><path d="M0.7 5 H9.3 M5 0.7 Q2.2 5 5 9.3 Q7.8 5 5 0.7" fill="none" stroke="#e3262b" stroke-width="0.9"/></svg>
        www.beaconsignalworks.com
      </li>
    </ul>

    <div class="front-mark"><span class="mark-dot"></span><span>Beacon<br>Signal</span></div>
  </section>

  <section class="card card--back" aria-label="Business card back">
    <div class="back-mark"><span class="mark-dot"></span><span>Beacon Signal<br>Works LLC</span></div>
  </section>

</body>
</html>
```